Website for Vornelix Capital, my new firm that raises money from investors to buy, build, own an...

Vornelix Capital needs a website! We are a new company with very experienced people, who invest in, own and build hotel properties, as well as apartments and other commercial real estate. We seek investors for our projects, and we provide safe, secure returns on their investment in our projects. Our new logo is designed to exhibit strength, class and security, and would like our website to continue on this theme. Our name, Vornelix, is a word-play on a Greek word “aristeia”, which means “excellence” and “a warriors finest moment of glory in war”. If you are in business, you realize that much of it is like war, with strategy and moves and opponents and competitors, and ever-changing economic conditions and threats that make business very much like war. We like to think that we are good at business (war), and so have named our company “Vornelix”, using the founders last name and the word “aristeia” combined. Another definition of "aristeia" is "performing at the peak of one's potential after a long struggle"...again, much like business in real life! The website design should exhibit financial security, smart moves, and positive growth towards a bright future.

Target Market(s)

The target market is smart and wealthy investors, with others such as brokers, cities and government agencies, lenders, sellers, partners, etc also looking at it.

Industry/Entity Type

Investment

Number of Pages Required

5+ page

Font styles to use
Sans Serif

Colors
fec214

Requirements
Must have
• Our website should have a landing page, a "about" or bio page, a projects page and a contact us page. Our new logo uses the colors black and gold, so this should be factored in to our site. The site should be simple, yet impactful and impressive. I have actually two logos, which can be mixed and interchanged in a complimentary way, each with their own unique look.
Nice to have
• I have uploaded a couple screenshots of a website i like, and the simplicity I mention.
Should not have
• The site should not be flashy or complicated or complex or "busy"

```html
<!DOCTYPE html>
<html lang="en">
<head>
<meta charset="utf-8">
<title>Vornelix Capital</title>
<link href="https://fonts.googleapis.com/css2?family=Raleway:wght@400;500;600;700;800&family=Exo:wght@500;600&display=swap" rel="stylesheet">
<style>
:root{
  --gold:#c9982b;
  --gold-band:#cfa235;
  --ink:#111111;
  --text:#6a6a6a;
  --footer:#0d0d0d;
  --footer-base:#050505;
  --white:#ffffff;
}
*{margin:0;padding:0;box-sizing:border-box}
html,body{width:753px;height:1200px;overflow:hidden;background:var(--white)}
body{position:relative;font-family:"Raleway",sans-serif;color:var(--ink)}
.abs{position:absolute}

/* header */
.site-header{position:absolute;left:0;top:0;width:753px;height:85px;background:var(--white)}
.social{position:absolute;display:flex;gap:5px}
.social span{width:25px;height:25px;border-radius:50%;border:1px solid var(--gold)}
.social span:first-child{background:var(--gold)}
.header-social{left:49px;top:29px}
.brand{position:absolute;left:0;width:753px;top:22px;text-align:center}
.brand-name{font-family:"Exo",sans-serif;font-weight:600;font-size:16px;letter-spacing:1px;color:var(--ink)}
.brand-sub{font-size:6px;letter-spacing:3px;color:var(--gold);font-weight:700;margin-top:1px}
.call{position:absolute;left:578px;top:27px;display:flex;gap:6px}
.call-label{font-size:10px;color:#333}
.call-number{font-family:"Exo",sans-serif;font-size:12px;color:var(--gold);letter-spacing:1px;margin-top:2px}

/* nav */
.main-nav{position:absolute;top:85px;left:0;width:753px;height:39px;background:var(--gold);display:flex;justify-content:center;align-items:center;gap:22px}
.main-nav a{color:var(--white);font-size:10.5px;font-weight:500;text-decoration:none;letter-spacing:.2px}
.main-nav a.active::before{content:"";display:inline-block;width:4px;height:4px;border-radius:50%;background:var(--white);margin-right:8px;vertical-align:middle}

/* hero */
.hero{position:absolute;top:124px;left:0;width:753px;height:301px;background:linear-gradient(180deg,#6f7480 0%,#868a92 35%,#4d5560 60%,#2f343b 100%)}
.hero-caption{position:absolute;left:0;bottom:0;width:753px;height:46px;background:rgba(30,32,36,.6);display:flex;justify-content:center;align-items:center;gap:30px}
.hero-caption h2{color:var(--white);font-weight:800;font-size:15px;letter-spacing:.3px}

/* welcome */
.welcome{position:absolute;top:463px;left:0;width:753px;text-align:center}
.welcome .kicker{color:var(--gold);font-size:13px;font-weight:600}
.welcome h1{font-family:"Exo",sans-serif;font-weight:600;font-size:26px;letter-spacing:.5px;margin-top:4px}
.welcome p{width:510px;margin:10px auto 0;font-size:8.6px;line-height:17px;color:var(--text)}
.services{position:absolute;top:590px;left:0;width:753px;display:flex;justify-content:center;gap:22px}
.service{width:130px;text-align:center}
.service-icon{width:59px;height:59px;border-radius:50%;background:var(--gold);margin:0 auto;display:flex;align-items:center;justify-content:center}
.service h3{font-size:10px;font-weight:600;margin-top:13px;color:#222}
.service p{font-size:8.6px;line-height:14px;color:var(--text);margin-top:3px}

/* projects */
.projects{position:absolute;top:745px;left:0;width:753px;height:242px;background:linear-gradient(180deg,#d3a63a 0%,#c99a2f 60%,#b98b28 100%)}
.projects h2{position:absolute;top:38px;width:753px;text-align:center;font-family:"Exo",sans-serif;font-weight:600;font-size:26px;color:var(--white)}
.project{position:absolute;top:87px;width:157px;height:117px}
.p1{left:48px;background:linear-gradient(180deg,#2a3340,#4a3830 70%,#2b2624)}
.p2{left:215px;background:linear-gradient(180deg,#5b92cf,#9cc0e3 45%,#6f8a73 90%)}
.p3{left:381px;background:linear-gradient(180deg,#6c8bb0,#2c3035 50%,#5a4c3c)}
.p4{left:548px;background:linear-gradient(180deg,#4c5b74,#808da0 55%,#4a4a4c)}
.zoom{position:absolute;left:61px;top:41px;width:35px;height:35px;border-radius:50%;border:1.5px solid var(--white);display:flex;align-items:center;justify-content:center}
.arrow{position:absolute}

/* footer */
.site-footer{position:absolute;top:987px;left:0;width:753px;height:175px;background:var(--footer)}
.footer-brand{position:absolute;left:63px;top:42px;width:120px;text-align:center}
.footer-brand .brand-name{color:var(--white);font-size:13px}
.footer-social{left:80px;top:97px}
.footer-col{position:absolute;top:27px}
.footer-col h4{color:var(--gold);font-size:11px;font-weight:600}
.sitemap{left:216px}
.sitemap ul{list-style:none;margin-top:14px}
.sitemap li{font-size:9px;color:#cfcfcf;height:18.5px;padding-left:12px;position:relative}
.sitemap li::before{content:"";position:absolute;left:0;top:3px;width:4px;height:4px;border-radius:50%;background:var(--gold)}
.contact{left:383px}
.contact-item{display:flex;align-items:center;gap:10px;position:absolute;left:-2px;font-size:9px;color:#cfcfcf;line-height:13px;width:170px}
.contact-icon{flex:none;width:26px;height:26px;border-radius:50%;border:1px solid var(--gold);display:flex;align-items:center;justify-content:center}
.newsletter{left:549px;width:158px}
.newsletter p{font-size:8.6px;line-height:13px;color:#cfcfcf;margin-top:15px}
.email-field{margin-top:6px;margin-left:-2px;width:157px;height:27px;background:var(--white);font-size:8.6px;color:#444;padding:8px 10px}
.subscribe{margin-top:3px;margin-left:-2px;width:98px;height:26px;background:var(--gold);color:var(--white);font-family:"Exo",sans-serif;font-weight:600;font-size:12px;display:flex;align-items:center;justify-content:center}
.footer-base{position:absolute;top:1162px;left:0;width:753px;height:38px;background:var(--footer-base);text-align:center;font-size:8.5px;line-height:38px;color:#9a9a9a}
.footer-base strong{color:var(--white);font-weight:500}
</style>
</head>
<body>

<header class="site-header">
  <div class="social header-social"><span></span><span></span><span></span></div>
  <div class="brand">
    <div class="brand-name">VORNELIX</div>
    <div class="brand-sub">CAPITAL</div>
  </div>
  <div class="call">
    <svg width="24" height="26" viewBox="0 0 24 24"><path fill="#c9982b" d="M6.6 10.8c1.4 2.8 3.8 5.1 6.6 6.6l2.2-2.2c.3-.3.7-.4 1-.2 1.1.4 2.3.6 3.6.6.6 0 1 .4 1 1V20c0 .6-.4 1-1 1C10.6 21 3 13.4 3 4c0-.6.4-1 1-1h3.5c.6 0 1 .4 1 1 0 1.3.2 2.5.6 3.6.1.3 0 .7-.2 1z"/></svg>
    <div>
      <div class="call-label">Call Us Today :</div>
      <div class="call-number">123 456 7890</div>
    </div>
  </div>
</header>

<nav class="main-nav">
  <a class="active" href="#">HOME</a>
  <a href="#">ABOUT US</a>
  <a href="#">PROJECTS</a>
  <a href="#">CONTACT US</a>
</nav>

<section class="hero" role="img" aria-label="Modern glass office building at dusk">
  <div class="hero-caption">
    <svg width="10" height="18" viewBox="0 0 10 18"><path d="M8 1L2 9l6 8" stroke="#fff" stroke-width="1.3" fill="none"/></svg>
    <h2>WE PROVIDE SAFE, SECURE RETURNS</h2>
    <svg width="10" height="18" viewBox="0 0 10 18"><path d="M2 1l6 8-6 8" stroke="#fff" stroke-width="1.3" fill="none"/></svg>
  </div>
</section>

<section class="welcome">
  <div class="kicker">WELCOME TO</div>
  <h1>VORNELIX CAPITAL</h1>
  <p>Lorem Ipsum is simply dummy text of the printing and typesetting industry. Lorem Ipsum has been the industry's standard dummy text ever since the 1500s, when an unknown printer took a galley of type and scrambled it to make a type specimen book It has survived not only five centuries</p>
</section>

<section class="services">
  <div class="service">
    <div class="service-icon">
      <svg width="30" height="32" viewBox="0 0 30 32" fill="#fff"><rect x="4" y="4" width="12" height="26"/><rect x="16" y="12" width="10" height="18"/><g fill="#c9982b"><rect x="6" y="7" width="3" height="3"/><rect x="11" y="7" width="3" height="3"/><rect x="6" y="13" width="3" height="3"/><rect x="11" y="13" width="3" height="3"/><rect x="6" y="19" width="3" height="3"/><rect x="11" y="19" width="3" height="3"/><rect x="18" y="15" width="2" height="2"/><rect x="22" y="15" width="2" height="2"/><rect x="18" y="20" width="2" height="2"/><rect x="22" y="20" width="2" height="2"/><rect x="8" y="25" width="4" height="5"/></g></svg>
    </div>
    <h3>BUILD HOTEL PROPERTIES</h3>
    <p>Lorem Ipsum is simply dummy text of the printing.</p>
  </div>
  <div class="service">
    <div class="service-icon">
      <svg width="30" height="32" viewBox="0 0 30 32" fill="#fff"><rect x="6" y="3" width="18" height="27"/><g fill="#c9982b"><rect x="9" y="7" width="12" height="2"/><rect x="9" y="12" width="12" height="2"/><rect x="9" y="17" width="12" height="2"/><rect x="12" y="23" width="6" height="7"/></g></svg>
    </div>
    <h3>APARTMENTS</h3>
    <p>Lorem Ipsum is simply dummy text of the printing.</p>
  </div>
  <div class="service">
    <div class="service-icon">
      <svg width="32" height="32" viewBox="0 0 32 32" fill="#fff"><path d="M16 3L3 13h3v17h20V13h3z"/><g fill="#c9982b"><rect x="9" y="15" width="3" height="3"/><rect x="14.5" y="15" width="3" height="3"/><rect x="20" y="15" width="3" height="3"/><rect x="9" y="20" width="3" height="3"/><rect x="20" y="20" width="3" height="3"/><rect x="14" y="21" width="4" height="9"/><rect x="14.5" y="9" width="3" height="3"/></g></svg>
    </div>
    <h3>COMMERCIAL REAL ESTATE</h3>
    <p>Lorem Ipsum is simply dummy text of the printing.</p>
  </div>
</section>

<section class="projects" role="img" aria-label="City skyline tinted in gold">
  <h2>OUR PROJECTS</h2>
  <svg class="arrow" style="left:30px;top:130px" width="10" height="18" viewBox="0 0 10 18"><path d="M8 1L2 9l6 8" stroke="#fff" stroke-width="1.5" fill="none"/></svg>
  <div class="project p1" role="img" aria-label="Brick apartment building at night">
    <div class="zoom"><svg width="14" height="14" viewBox="0 0 14 14"><circle cx="6" cy="6" r="4.2" stroke="#fff" stroke-width="2" fill="none"/><path d="M9 9l4 4" stroke="#fff" stroke-width="2"/></svg></div>
  </div>
  <div class="project p2" role="img" aria-label="Glass office building under blue sky"></div>
  <div class="project p3" role="img" aria-label="Modern apartment block with balconies"></div>
  <div class="project p4" role="img" aria-label="Glass corporate campus at dusk"></div>
  <svg class="arrow" style="left:715px;top:130px" width="10" height="18" viewBox="0 0 10 18"><path d="M2 1l6 8-6 8" stroke="#fff" stroke-width="1.5" fill="none"/></svg>
</section>

<footer class="site-footer">
  <div class="footer-brand">
    <div class="brand-name">VORNELIX</div>
    <div class="brand-sub">CAPITAL</div>
  </div>
  <div class="social footer-social"><span></span><span></span><span></span></div>

  <div class="footer-col sitemap">
    <h4>SITEMAP</h4>
    <ul><li>Home</li><li>About Us</li><li>Projects</li><li>Contact Us</li></ul>
  </div>

  <div class="footer-col contact">
    <h4>CONTCT US</h4>
    <div class="contact-item" style="top:25px">
      <span class="contact-icon"><svg width="10" height="14" viewBox="0 0 10 14"><path fill="#c9982b" d="M5 0a5 5 0 0 0-5 5c0 3.8 5 9 5 9s5-5.2 5-9a5 5 0 0 0-5-5zm0 7a2 2 0 1 1 0-4 2 2 0 0 1 0 4z"/></svg></span>
      <span>101 - lorem ipsum simple text simple dummy text.</span>
    </div>
    <div class="contact-item" style="top:63px">
      <span class="contact-icon"><svg width="13" height="13" viewBox="0 0 24 24"><path fill="#c9982b" d="M6.6 10.8c1.4 2.8 3.8 5.1 6.6 6.6l2.2-2.2c.3-.3.7-.4 1-.2 1.1.4 2.3.6 3.6.6.6 0 1 .4 1 1V20c0 .6-.4 1-1 1C10.6 21 3 13.4 3 4c0-.6.4-1 1-1h3.5c.6 0 1 .4 1 1 0 1.3.2 2.5.6 3.6.1.3 0 .7-.2 1z"/></svg></span>
      <span>+1 123 456 7890</span>
    </div>
    <div class="contact-item" style="top:98px">
      <span class="contact-icon"><svg width="13" height="10" viewBox="0 0 13 10"><rect width="13" height="10" rx="1" fill="#c9982b"/><path d="M0.5 1l6 4.5 6-4.5" stroke="#0d0d0d" stroke-width="1.2" fill="none"/></svg></span>
      <span>info@VORNELIX.com</span>
    </div>
  </div>

  <div class="footer-col newsletter">
    <h4>NEWSLETTER</h4>
    <p>Would you like to recieve our exclusive news and updates !</p>
    <div class="email-field">Enter Email *</div>
    <div class="subscribe">SUBSCRIBE</div>
  </div>
</footer>

<div class="footer-base">©<strong>VORNELIX CAPITAL</strong> - 2018 All Right Reserved.</div>

</body>
</html>
```